Business Card Design - VNT (company name)

Over 20 years of progressive technology design, migration and management experience that drives business objectives and streamlines operations. Continuously challenge conventions to meet and exceed business security, availability and functionality requirements. Maintain exceptional vendor relationships to ensure ongoing knowledge of emerging products and to secure preferred service agreements. Recruit and utilize top talent and foster a collegial environment that advances innovation and performance excellence. design logo using 3 arrows of different colors green, gold, blue

Industry/Entity Type

Progressive

Contact Information for Business Card

Martin K. Osgood
IT Strategist / Consultant

626.583.2907 MOsgood@vntosgood.example 4817 Brenning Court Pasadena, CA 91104

Colors
0255a3
f37122
fece3e

Requirements
Must have
• Note NEW EMAIL ADDRESS
• MOsgood@vntosgood.example
• NOTE NEW ORDER of the work I do.
• Infrastructure – Systems – Cybersecurity
Nice to have
• main color should be orange

```html
<!DOCTYPE html>
<html lang="en">
<head>
<meta charset="utf-8">
<title>VNT Business Card</title>
<link rel="stylesheet" href="https://fonts.googleapis.com/css2?family=Open+Sans:wght@400;600&family=PT+Serif:wght@400;700&display=swap">
<style>
  :root {
    --brand-orange: #f07b2a;
    --accent-orange: #f37122;
    --brand-blue: #0255a3;
    --brand-gold: #fece3e;
    --paper: #ffffff;
    --backdrop: #e9e6e1;
    --text-light: #ffffff;
  }
  * { margin: 0; padding: 0; box-sizing: border-box; }
  html, body { width: 1200px; height: 900px; overflow: hidden; }
  body {
    background: var(--backdrop);
    font-family: "Open Sans", Arial, sans-serif;
    display: flex;
    align-items: center;
    justify-content: center;
    gap: 50px;
  }
  .card {
    position: relative;
    width: 525px;
    height: 300px;
    overflow: hidden;
    box-shadow: 0 6px 18px rgba(0,0,0,0.18);
  }

  /* Front */
  .card-front { background: var(--brand-orange); }
  .front-brand {
    position: absolute;
    left: 0; right: 0; top: 88px;
    display: flex; align-items: center; justify-content: center; gap: 12px;
    color: var(--text-light);
    font-weight: 600;
    font-size: 56px;
    letter-spacing: 2px;
  }
  .brand-dot {
    width: 22px; height: 22px; border-radius: 50%;
    background: var(--text-light);
  }
  .services {
    position: absolute;
    left: 0; right: 0; bottom: 30px;
    text-align: center;
    color: var(--text-light);
    font-size: 14px;
    letter-spacing: 0.2px;
  }

  /* Back */
  .card-back { background: var(--paper); }
  .back-shape { position: absolute; inset: 0; }
  .back-brand {
    position: absolute;
    left: 62px; top: 118px;
    display: flex; align-items: center; gap: 10px;
    color: var(--brand-blue);
    font-weight: 600;
    font-size: 44px;
    letter-spacing: 1px;
  }
  .back-brand .brand-dot { background: var(--accent-orange); width: 18px; height: 18px; }
  .holder {
    position: absolute;
    right: 24px; top: 80px;
    color: var(--text-light);
    font-family: "PT Serif", Georgia, serif;
  }
  .holder-name { font-weight: 700; font-size: 19px; letter-spacing: 0.5px; white-space: nowrap; }
  .holder-role { font-size: 13px; margin-left: 22px; white-space: nowrap; }
  .contacts {
    position: absolute;
    left: 232px; bottom: 22px;
    list-style: none;
    color: var(--text-light);
    font-size: 14px;
    line-height: 1;
  }
  .contacts li { display: flex; align-items: center; gap: 9px; margin-top: 6px; white-space: nowrap; }
  .contacts li.contact-continued { padding-left: 25px; }
  .contact-icon {
    width: 16px; height: 16px; border-radius: 3px;
    background: var(--paper);
    display: flex; align-items: center; justify-content: center;
    flex-shrink: 0;
  }
  .contact-icon svg { width: 11px; height: 11px; }
</style>
</head>
<body>

  <section class="card card-front" aria-label="Card front">
    <div class="front-brand"><span class="brand-dot"></span>VNT</div>
    <p class="services">IT Strategist | Consultant | Infrastructure | Systems | Cybersecurity</p>
  </section>

  <section class="card card-back" aria-label="Card back">
    <svg class="back-shape" viewBox="0 0 525 300" preserveAspectRatio="none" aria-hidden="true">
      <polygon points="322,12 525,70 525,300 150,300" fill="var(--accent-orange)"/>
      <polygon points="328,22 525,78 525,300 162,300" fill="var(--brand-blue)"/>
    </svg>

    <div class="back-brand"><span class="brand-dot"></span>VNT</div>

    <div class="holder">
      <p class="holder-name">MARTIN K. OSGOOD</p>
      <p class="holder-role">IT Strategist / Consultant</p>
    </div>

    <ul class="contacts">
      <li>
        <span class="contact-icon"><svg viewBox="0 0 12 12"><path d="M3 1 L5 3.5 L4 5 Q5 7 7 8 L8.5 7 L11 9 L9.5 11 Q4 10.5 1 3 Z" fill="var(--accent-orange)"/></svg></span>
        626.583.2907
      </li>
      <li>
        <span class="contact-icon"><svg viewBox="0 0 12 12"><rect x="1" y="2.5" width="10" height="7" rx="1" fill="var(--accent-orange)"/><path d="M1.5 3 L6 6.5 L10.5 3" stroke="#fff" stroke-width="1" fill="none"/></svg></span>
        MOsgood@vntosgood.example
      </li>
      <li>
        <span class="contact-icon"><svg viewBox="0 0 12 12"><path d="M6 11 Q2 6.5 2 4.5 A4 4 0 0 1 10 4.5 Q10 6.5 6 11 Z" fill="var(--accent-orange)"/><circle cx="6" cy="4.5" r="1.4" fill="#fff"/></svg></span>
        4817 Brenning Court
      </li>
      <li class="contact-continued">Pasadena, CA 91104</li>
    </ul>
  </section>

</body>
</html>
```